Need Flyer for Our Real estate Agency

Need to run General Campaign for our agency with Start of New Year as our theme ..Must have an agent's picture on the DL..
Address:
27 / 486Brindle rd, Marsden VIC 3047
Ph:03 9412 7306
email:info@kovalinrealestate.com.au
www.kovalinrealestate.com.au
Something like as attached picture..
Target Market(s)
Home Buyers
Industry/Entity Type
Real Estate Agent
Requirements
Must have
- Our Logo Colours

```html
<!DOCTYPE html>
<html lang="en">
<head>
<meta charset="utf-8">
<title>Kovalin Real Estate – New Year DL Flyer</title>
<link href="https://fonts.googleapis.com/css2?family=Tinos:wght@400;700&display=swap" rel="stylesheet">
<style>
  :root {
    --page-bg: #c3c3c5;
    --navy: #1b2a63;
    --navy-deep: #14204f;
    --maroon: #7c0e1e;
    --maroon-dark: #4e0712;
    --white: #ffffff;
    --text-soft: #e6e9f3;
  }
  html, body {
    margin: 0;
    padding: 0;
    width: 800px;
    height: 1200px;
    overflow: hidden;
    background: var(--page-bg);
    font-family: "Tinos", "Times New Roman", serif;
  }
  .canvas {
    position: relative;
    width: 800px;
    height: 1200px;
  }
  .flyer {
    position: absolute;
    left: 60px;
    width: 680px;
    height: 340px;
    box-shadow: 0 6px 16px rgba(0,0,0,0.35);
    overflow: hidden;
  }
  .flyer--front { top: 220px; }
  .flyer--back  { top: 640px; }
  .flyer__shapes {
    position: absolute;
    inset: 0;
    width: 680px;
    height: 340px;
    display: block;
  }
  .brand {
    position: absolute;
    left: 0;
    width: 264px;
    top: 108px;
    text-align: center;
    color: var(--white);
    font-size: 40px;
    font-weight: 400;
    letter-spacing: 4px;
    line-height: 1;
    white-space: nowrap;
  }
  .brand__mark {
    display: inline-block;
    width: 8px;
    height: 8px;
    background: var(--maroon);
    vertical-align: middle;
    margin-right: 10px;
    position: relative;
    top: -4px;
  }
  .headline {
    position: absolute;
    left: 35px;
    top: 196px;
    margin: 0;
    color: var(--white);
    font-size: 23px;
    font-weight: 700;
    line-height: 1.25;
  }
  .blurb {
    position: absolute;
    left: 35px;
    top: 275px;
    width: 285px;
    margin: 0;
    color: var(--text-soft);
    font-size: 10.5px;
    line-height: 1.3;
  }
  .contact-list {
    position: absolute;
    left: 32px;
    top: 202px;
    margin: 0;
    padding: 0;
    list-style: none;
  }
  .contact-list::before {
    content: "";
    position: absolute;
    left: 8px;
    top: 10px;
    bottom: 10px;
    width: 1.5px;
    background: var(--white);
  }
  .contact-list__item {
    position: relative;
    display: flex;
    align-items: center;
    height: 30px;
    color: var(--white);
    font-size: 14px;
    white-space: nowrap;
  }
  .contact-list__icon {
    position: relative;
    width: 17px;
    height: 17px;
    margin-right: 13px;
    flex: none;
  }
</style>
</head>
<body>
<main class="canvas">

  <section class="flyer flyer--front">
    <svg class="flyer__shapes" viewBox="0 0 680 340">
      <defs>
        <linearGradient id="officeTone" x1="0" y1="0" x2="1" y2="0">
          <stop offset="0" stop-color="#c9d3de"/>
          <stop offset="0.6" stop-color="#dfe5ec"/>
          <stop offset="1" stop-color="#eef1f5"/>
        </linearGradient>
        <radialGradient id="agentTone" cx="0.72" cy="0.75" r="0.45">
          <stop offset="0" stop-color="#223566"/>
          <stop offset="0.7" stop-color="#2b3f74" stop-opacity="0.9"/>
          <stop offset="1" stop-color="#2b3f74" stop-opacity="0"/>
        </radialGradient>
        <linearGradient id="bandFront" x1="0" y1="0" x2="1" y2="0">
          <stop offset="0" stop-color="var(--maroon-dark)"/>
          <stop offset="1" stop-color="var(--maroon)"/>
        </linearGradient>
      </defs>
      <g role="img" aria-label="Photo of a smiling real estate agent in a navy suit, arms crossed, in front of office windows with a city view">
        <rect x="300" y="0" width="380" height="340" fill="url(#officeTone)"/>
        <rect x="300" y="0" width="380" height="340" fill="url(#agentTone)"/>
      </g>
      <polygon points="0,0 334,0 437,170 334,340 0,340" fill="url(#bandFront)"/>
      <polygon points="0,0 302,0 406,170 302,340 0,340" fill="var(--navy)"/>
    </svg>
    <div class="brand"><span class="brand__mark"></span>KOVALIN</div>
    <h1 class="headline">Curious to Know what<br>your home is worth?</h1>
    <p class="blurb">Start the New Year with a free, no-obligation appraisal of your home from our friendly local team.</p>
  </section>

  <section class="flyer flyer--back">
    <svg class="flyer__shapes" viewBox="0 0 680 340">
      <defs>
        <linearGradient id="suitTone" x1="0" y1="0" x2="1" y2="1">
          <stop offset="0" stop-color="#1e2a45"/>
          <stop offset="0.5" stop-color="#3a4a66"/>
          <stop offset="1" stop-color="#1a2438"/>
        </linearGradient>
        <radialGradient id="houseTone" cx="0.62" cy="0.55" r="0.4">
          <stop offset="0" stop-color="#de4f4c"/>
          <stop offset="0.5" stop-color="#c98f7c"/>
          <stop offset="1" stop-color="#c98f7c" stop-opacity="0"/>
        </radialGradient>
        <linearGradient id="bandBack" x1="0" y1="0" x2="1" y2="0">
          <stop offset="0" stop-color="var(--maroon-dark)"/>
          <stop offset="1" stop-color="var(--maroon)"/>
        </linearGradient>
      </defs>
      <g role="img" aria-label="Photo of two hands sheltering a small red model house">
        <rect x="300" y="0" width="380" height="340" fill="url(#suitTone)"/>
        <rect x="300" y="0" width="380" height="340" fill="url(#houseTone)"/>
      </g>
      <polygon points="0,0 334,0 437,170 334,340 0,340" fill="url(#bandBack)"/>
      <polygon points="0,0 302,0 406,170 302,340 0,340" fill="var(--navy)"/>
    </svg>
    <div class="brand"><span class="brand__mark"></span>KOVALIN</div>
    <ul class="contact-list">
      <li class="contact-list__item">
        <svg class="contact-list__icon" viewBox="0 0 18 18"><circle cx="9" cy="9" r="8.5" fill="var(--white)"/><path d="M9 4a3 3 0 0 0-3 3c0 2.3 3 6 3 6s3-3.7 3-6a3 3 0 0 0-3-3z" fill="var(--navy)"/><circle cx="9" cy="7" r="1.1" fill="var(--white)"/></svg>
        27 / 486Brindle rd, Marsden VIC 3047
      </li>
      <li class="contact-list__item">
        <svg class="contact-list__icon" viewBox="0 0 18 18"><circle cx="9" cy="9" r="8.5" fill="var(--white)"/><path d="M6 4.5l1.8 2.2-1 1.2c.6 1.3 1.5 2.2 2.8 2.8l1.2-1 2.2 1.8-1 1.5c-3.4-.3-6.2-3.1-6.5-6.5z" fill="var(--navy)"/></svg>
        03 9412 7306
      </li>
      <li class="contact-list__item">
        <svg class="contact-list__icon" viewBox="0 0 18 18"><circle cx="9" cy="9" r="8.5" fill="var(--white)"/><rect x="4.5" y="6" width="9" height="6" fill="none" stroke="var(--navy)" stroke-width="1.2"/><path d="M4.5 6l4.5 3.5L13.5 6" fill="none" stroke="var(--navy)" stroke-width="1.2"/></svg>
        info@kovalinrealestate.com.au
      </li>
      <li class="contact-list__item">
        <svg class="contact-list__icon" viewBox="0 0 18 18"><circle cx="9" cy="9" r="8.5" fill="var(--white)"/><circle cx="9" cy="9" r="4.5" fill="none" stroke="var(--navy)" stroke-width="1.1"/><ellipse cx="9" cy="9" rx="2" ry="4.5" fill="none" stroke="var(--navy)" stroke-width="1"/><path d="M4.5 9h9" stroke="var(--navy)" stroke-width="1"/></svg>
        www.kovalinrealestate.com.au
      </li>
    </ul>
  </section>

</main>
</body>
</html>
```